Quorva - corporate Business Card

We need a good look and innovative business card for a new start up company based in Los Angeles called "Quorva". We are in a payment business, including payment card, app, and ewallet. We are expert in online payment and Card not present (CNP) transaction.
We need an innovative, modern business card.

Our logo font is Aero Matics

Target Market(s)

Startup - Bank - Online Payment - Card Manufacturing

Industry/Entity Type

Startup

Contact Information for Business Card

phone: 555 014 7396 - Address: 4172 Marlowe blvd, Ardenvale, OR 90299

Requirements
Must have
• Message: innovative, professional, expert, high tech, trust, online payment expert, security
Nice to have
• no comment
Should not have
• no Comment

```html
<!DOCTYPE html>
<html lang="en">
<head>
<meta charset="utf-8">
<title>Quorva — Business Card</title>
<link rel="stylesheet" href="https://fonts.googleapis.com/css2?family=Roboto:wght@400;500;700&display=swap">
<style>
  :root {
    --brand-red: #c61f30;
    --ink: #5a5a5c;
    --paper: #ffffff;
    --backdrop: #2b2b2d;
    --rule: #d8a0a6;
  }
  * { box-sizing: border-box; margin: 0; padding: 0; }
  html, body {
    width: 1200px;
    height: 950px;
    overflow: hidden;
    background: var(--backdrop);
    font-family: "Roboto", Arial, sans-serif;
  }
  .stage {
    width: 1200px;
    height: 950px;
    display: flex;
    flex-direction: column;
    align-items: center;
    justify-content: center;
    gap: 50px;
  }
  .card {
    position: relative;
    width: 700px;
    height: 400px;
    background: var(--paper);
  }

  /* Front */
  .identity {
    position: absolute;
    top: 58px;
    left: 380px;
    display: flex;
    align-items: center;
  }
  .identity__mark {
    width: 62px;
    height: 62px;
    border-radius: 50%;
    background: var(--brand-red);
  }
  .identity__divider {
    width: 1px;
    height: 62px;
    background: var(--rule);
    margin: 0 16px 0 18px;
  }
  .identity__name {
    color: var(--brand-red);
    font-weight: 700;
    font-size: 19px;
    letter-spacing: 0.5px;
    text-transform: uppercase;
    line-height: 1.1;
  }
  .identity__role {
    color: var(--ink);
    font-size: 14px;
    letter-spacing: 0.6px;
    text-transform: uppercase;
    margin-top: 3px;
  }
  .contact {
    position: absolute;
    left: 40px;
    bottom: 38px;
    list-style: none;
    color: var(--ink);
    font-size: 14px;
    line-height: 1.65;
  }
  .contact__label {
    color: var(--brand-red);
    font-weight: 700;
  }

  /* Back */
  .card--back {
    display: flex;
    align-items: center;
    justify-content: center;
  }
  .wordmark {
    display: flex;
    align-items: center;
    gap: 22px;
  }
  .wordmark__dot {
    width: 132px;
    height: 132px;
    border-radius: 50%;
    background: var(--brand-red);
  }
  .wordmark__name {
    color: var(--brand-red);
    font-weight: 500;
    font-size: 104px;
    letter-spacing: 1px;
    line-height: 1;
  }
</style>
</head>
<body>
<main class="stage">
  <section class="card card--front" aria-label="Business card front">
    <div class="identity">
      <div class="identity__mark" aria-hidden="true"></div>
      <div class="identity__divider" aria-hidden="true"></div>
      <div class="identity__text">
        <p class="identity__name">Mara Velt</p>
        <p class="identity__role">President</p>
      </div>
    </div>
    <ul class="contact">
      <li><span class="contact__label">P :</span> 555 014 7396</li>
      <li><span class="contact__label">E :</span> mara@quorva.com <span class="contact__label">W :</span> www.quorva.com</li>
      <li>4172 Marlowe blvd, Ardenvale, OR 90299</li>
    </ul>
  </section>

  <section class="card card--back" aria-label="Business card back">
    <div class="wordmark">
      <div class="wordmark__dot" aria-hidden="true"></div>
      <span class="wordmark__name">quorva</span>
    </div>
  </section>
</main>
</body>
</html>
```